New Alcoholic Spiked Seltzer Line

We need a can design for a line of low calorie alcoholic seltzer. This product is a sparkling water and vodka drink with no sugar added in a slim 12 oz can.

This is a lighter, healthier, alternative to the sugary ready-to-drinks on the market. The product contains only 3 ingredients: Vodka, Water and Natural Flavors. It has only 100 calories but still has 5% alcohol, so you don't need to sacrifice alcohol to cut calories.

This product also does not contain any preservatives.

We want this design to communicate the following objectives to the consumer and in this order:

1. Appetizing product
2.Low calorie
3.Communicate the type of beverage (Spiked Seltzer)

The brand name of the product is VELKA.

The flavor of the product needed to be used for the design is Mango-Orange.

Comparable products are:

www.brindlefizzworks.example/
https://www.quorvabubbles.example
https://pelnavo.example/

The designs should not infringe or copy the creative directions of the products mentionned above. They are only given so that you can better understand the type of product we are developing.

Target Market(s)

Young Professional women between the ages of 25 and 44

Industry/Entity Type

Product

Colors

Designer to choose colors to be used in the design.

Requirements
Must have
• Design extendibility, meaning it can be adapted for other flavors.
• This is a new category in the market we are targeting, so consumers must easily be able to identify what type of product this is.

```html
<!DOCTYPE html>
<html lang="en">
<head>
<meta charset="utf-8">
<title>VELKA Mango-Orange Spiked Seltzer – Can Label</title>
<link rel="stylesheet" href="https://fonts.googleapis.com/css2?family=Source+Sans+3:wght@400;600;700&display=swap">
<style>
  :root {
    --silver-light: #f1f2f3;
    --silver-mid: #d5d7d9;
    --silver-dark: #a9acaf;
    --charcoal: #3a3a3c;
    --band-black: #2a2a2b;
    --flavor-orange: #d2790f;
    --seltzer-maroon: #6e0f12;
    --rule-red: #e0262b;
    --copy-red: #b01c22;
    --footer-gold: #f2a93b;
  }
  * { margin: 0; padding: 0; box-sizing: border-box; }
  html, body {
    width: 1200px;
    height: 2546px;
    overflow: hidden;
    background: #ffffff;
  }
  .can-label {
    position: relative;
    width: 1200px;
    height: 2546px;
    overflow: hidden;
    font-family: "Source Sans 3", "Helvetica Neue", Arial, sans-serif;
    background: linear-gradient(90deg,
      var(--silver-dark) 0%,
      var(--silver-mid) 12%,
      var(--silver-light) 38%,
      var(--silver-light) 55%,
      var(--silver-mid) 80%,
      var(--silver-dark) 100%);
  }
  .brand-wordmark {
    position: absolute;
    left: 180px;
    top: 640px;
    width: 380px;
    height: 1420px;
    writing-mode: vertical-rl;
    transform: rotate(180deg);
    font-weight: 400;
    font-size: 430px;
    line-height: 380px;
    letter-spacing: 10px;
    color: var(--charcoal);
    white-space: nowrap;
  }
  .emblem-art {
    position: absolute;
    left: 575px;
    top: 1060px;
    width: 430px;
    height: 245px;
  }
  .product-info {
    position: absolute;
    left: 615px;
    top: 1370px;
    width: 420px;
  }
  .flavor-name {
    font-weight: 700;
    font-size: 46px;
    letter-spacing: 0.5px;
    color: var(--flavor-orange);
    line-height: 1.1;
  }
  .product-type {
    margin-top: 34px;
    font-weight: 400;
    font-size: 78px;
    line-height: 1.08;
    color: var(--seltzer-maroon);
  }
  .info-rule {
    width: 300px;
    height: 4px;
    background: var(--rule-red);
    margin: 30px 0;
  }
  .info-copy {
    font-size: 38px;
    line-height: 1.3;
    color: var(--copy-red);
  }
  .footer-band {
    position: absolute;
    left: 0;
    bottom: 0;
    width: 100%;
    height: 460px;
    background: var(--band-black);
    display: flex;
    justify-content: center;
    padding-top: 80px;
  }
  .footer-stats {
    font-size: 48px;
    font-weight: 400;
    color: var(--footer-gold);
    letter-spacing: 0.5px;
  }
</style>
</head>
<body>
  <main class="can-label">
    <div class="brand-wordmark">VELKA</div>

    <svg class="emblem-art" role="img" aria-label="Brand emblem illustration: a horned animal head over a red circle" viewBox="0 0 430 245">
      <defs>
        <radialGradient id="emblemTone" cx="50%" cy="50%" r="55%">
          <stop offset="0%" stop-color="#c8151b"/>
          <stop offset="60%" stop-color="#7a2a2c"/>
          <stop offset="100%" stop-color="#3a3a3c" stop-opacity="0.85"/>
        </radialGradient>
      </defs>
      <rect x="0" y="0" width="430" height="245" rx="24" fill="url(#emblemTone)"/>
    </svg>

    <section class="product-info">
      <p class="flavor-name">MANGO-ORANGE</p>
      <h1 class="product-type">Spiked<br>Seltzer</h1>
      <div class="info-rule"></div>
      <p class="info-copy">low calorie<br>alcoholic seltzer</p>
      <div class="info-rule"></div>
      <p class="info-copy">vodka, water &amp;<br>natural flavors</p>
      <div class="info-rule"></div>
    </section>

    <footer class="footer-band">
      <p class="footer-stats">5% alcohol - 100 calories</p>
    </footer>
  </main>
</body>
</html>
```